English and Spanish Language School Needs a Business Card

Need a business card design a startup company called Maribel Language School. The company will offer English and Spanish conversational level courses designed to make the learner feel comfortable with grammar and vocabulary. We would like to see a logo with some colour that should communicate learning, growth.

Target Market(s)

Consumers and businesses

Industry/Entity Type

Education

Contact Information for Business Card

TBD

Font styles to use
Serif

Requirements
Must have
• Include the following
• Logo
• Name
• Title
• Cellphone Number
• Office Phone number
• Email address
• Office Address

```html
<!DOCTYPE html>
<html lang="en">
<head>
<meta charset="utf-8">
<title>Maribel Language School – Business Card</title>
<link rel="stylesheet" href="https://fonts.googleapis.com/css2?family=Quicksand:wght@400;500;700&display=swap">
<style>
  :root {
    --page-bg: #e4e4e4;
    --card-light: #ffffff;
    --card-dark: #3b3b3d;
    --brand-red: #cc1720;
    --brand-teal: #17a2ad;
    --ink: #1d1d1d;
    --ink-on-dark: #f2f2f2;
  }
  * { box-sizing: border-box; margin: 0; padding: 0; }
  html, body {
    width: 1200px; height: 1021px; overflow: hidden;
    background: var(--page-bg);
    font-family: "Quicksand", sans-serif;
  }
  .sheet {
    position: relative; width: 1200px; height: 1021px;
  }
  .card {
    position: absolute; left: 220px; width: 760px; height: 434px;
    box-shadow: 0 6px 18px rgba(0,0,0,.18);
    overflow: hidden;
  }
  .card--front { top: 51px; background: var(--card-light); }
  .card--back { top: 536px; background: var(--card-dark); }

  /* Wordmark */
  .wordmark { position: absolute; color: var(--brand-red); font-weight: 700; line-height: 1; }
  .wordmark__name { display: block; }
  .wordmark__sub { display: block; }
  .card--front .wordmark { left: 70px; top: 178px; }
  .card--front .wordmark__name { font-size: 54px; letter-spacing: -1px; }
  .card--front .wordmark__sub { font-size: 20px; margin-top: 6px; padding-left: 4px; }

  .divider {
    position: absolute; left: 372px; top: 92px;
    width: 3px; height: 250px; background: var(--brand-teal);
  }

  .contact { position: absolute; left: 408px; top: 98px; color: var(--ink); }
  .contact__name { font-size: 30px; font-weight: 500; }
  .contact__title { font-size: 20px; color: var(--brand-teal); margin-top: 2px; margin-bottom: 20px; }
  .contact__list { list-style: none; }
  .contact__item {
    display: flex; align-items: center; gap: 12px;
    font-size: 19px; font-weight: 500; height: 32px;
  }
  .contact__icon { width: 18px; height: 18px; flex: none; }

  /* Back */
  .card--back .wordmark { left: 150px; top: 160px; }
  .card--back .wordmark__name { font-size: 86px; letter-spacing: -1px; }
  .card--back .wordmark__sub { font-size: 28px; margin-top: 8px; padding-left: 6px; }
  .back-rules { position: absolute; left: 0; top: 0; width: 760px; height: 434px; }
</style>
</head>
<body>
<main class="sheet">
  <section class="card card--front" aria-label="Business card front">
    <div class="wordmark">
      <span class="wordmark__name">Maribel</span>
      <span class="wordmark__sub">Language School</span>
    </div>
    <div class="divider"></div>
    <div class="contact">
      <p class="contact__name">Your Name</p>
      <p class="contact__title">Job Title</p>
      <ul class="contact__list">
        <li class="contact__item">
          <svg class="contact__icon" viewBox="0 0 20 20"><path fill="#cc1720" d="M2 8c0-3 3-5 8-5s8 2 8 5v1h-4V7H6v2H2zM4 10h12l1 7H3z"/></svg>
          000 000 0000
        </li>
        <li class="contact__item">
          <svg class="contact__icon" viewBox="0 0 20 20"><rect x="5" y="1.5" width="10" height="17" rx="2" fill="none" stroke="#cc1720" stroke-width="2"/><circle cx="10" cy="15" r="1.2" fill="#cc1720"/></svg>
          000 000 0000
        </li>
        <li class="contact__item">
          <svg class="contact__icon" viewBox="0 0 20 20"><rect x="1" y="4" width="18" height="12" fill="#cc1720"/><path d="M1 4l9 7 9-7" fill="none" stroke="#fff" stroke-width="1.6"/></svg>
          youremail@xyz.com
        </li>
        <li class="contact__item">
          <svg class="contact__icon" viewBox="0 0 20 20"><path fill="#cc1720" d="M10 1a6 6 0 0 0-6 6c0 5 6 12 6 12s6-7 6-12a6 6 0 0 0-6-6zm0 8.5A2.5 2.5 0 1 1 10 4.5a2.5 2.5 0 0 1 0 5z"/></svg>
          address, here- 0000
        </li>
      </ul>
    </div>
  </section>

  <section class="card card--back" aria-label="Business card back">
    <svg class="back-rules" viewBox="0 0 760 434" aria-hidden="true">
      <line x1="470" y1="238" x2="760" y2="238" stroke="#cc1720" stroke-width="5"/>
      <line x1="470" y1="250" x2="760" y2="250" stroke="#17a2ad" stroke-width="5"/>
    </svg>
    <div class="wordmark">
      <span class="wordmark__name">Maribel</span>
      <span class="wordmark__sub">Language School</span>
    </div>
  </section>
</main>
</body>
</html>
```